New signage for apartment community in the Pacific Northwest

Signage for an apartment community in the Pacific Northwest. It should have a contemporary northwest vibe with a fresh exciting feeling. We are open to the colors cayenne, white, charcoal and a splash of lime green. Sign to have the name 'VOLTE' with the address number 28351 smaller underneath. sign can include a shape under the name or a feeling of energy in the shape of the name.

Target Market(s)

Young urban professionals

Industry/Entity Type

Real Estate Development

Requirements
Must have
• eyecatching
Should not have
• anything too cute or too busy

```html
<!DOCTYPE html>
<html lang="en">
<head>
<meta charset="utf-8">
<title>Volte Apartments – Signage Concept</title>
<link href="https://fonts.googleapis.com/css2?family=Montserrat:wght@400;500;600&display=swap" rel="stylesheet">
<style>
  :root {
    --backdrop: #e0e0e0;
    --charcoal-top: #3d4b48;
    --charcoal-mid: #2e3b38;
    --charcoal-deep: #0e1411;
    --lime: #b4d334;
    --white: #ffffff;
    --caption: #5a5a5a;
  }
  html, body {
    margin: 0;
    padding: 0;
    overflow: hidden;
    background: var(--backdrop);
  }
  .canvas {
    position: relative;
    width: 1200px;
    height: 884px;
    background: var(--backdrop);
  }
  .signage {
    position: absolute;
    inset: 0;
    width: 1200px;
    height: 884px;
  }
  .panel {
    filter: drop-shadow(4px 5px 4px rgba(0, 0, 0, 0.35));
  }
  .frame-line {
    fill: none;
    stroke: var(--lime);
    stroke-width: 2;
  }
  .community-name {
    font-family: "Montserrat", sans-serif;
    font-weight: 600;
    font-size: 148px;
    letter-spacing: 6px;
    fill: var(--white);
  }
  .descriptor {
    font-family: "Montserrat", sans-serif;
    font-weight: 600;
    font-size: 40px;
    letter-spacing: 14.5px;
    fill: var(--lime);
  }
  .address-number {
    font-family: "Montserrat", sans-serif;
    font-weight: 500;
    font-size: 60px;
    letter-spacing: 22px;
    fill: var(--white);
  }
  .caption {
    position: absolute;
    left: 0;
    right: 0;
    top: 810px;
    margin: 0;
    text-align: center;
    font-family: "Montserrat", sans-serif;
    font-weight: 400;
    font-size: 15px;
    letter-spacing: 0.5px;
    color: var(--caption);
  }
</style>
</head>
<body>
<div class="canvas">
  <svg class="signage" viewBox="0 0 1200 884" xmlns="http://www.w3.org/2000/svg">
    <defs>
      <linearGradient id="forest-mist" x1="0" y1="0" x2="0" y2="1">
        <stop offset="0" stop-color="var(--charcoal-top)"/>
        <stop offset="0.55" stop-color="var(--charcoal-mid)"/>
        <stop offset="1" stop-color="var(--charcoal-deep)"/>
      </linearGradient>
      <linearGradient id="plaque-tone" x1="0" y1="0" x2="0" y2="1">
        <stop offset="0" stop-color="#2c3835"/>
        <stop offset="1" stop-color="#1d2724"/>
      </linearGradient>
    </defs>

    <!-- Main name sign -->
    <g class="panel">
      <path class="name-sign" role="img" aria-label="Misty evergreen forest on a hillside"
            fill="url(#forest-mist)"
            d="M149,91 H1052 A64,64 0 0 0 1116,155 V639 H84 V155 A64,64 0 0 0 149,91 Z"/>
    </g>
    <path class="frame-line"
          d="M170,123 H1031 A53,53 0 0 0 1084,176 V608 H116 V176 A54,54 0 0 0 170,123 Z"/>
    <text class="community-name" x="606" y="420" text-anchor="middle">VOLTE</text>
    <text class="descriptor" x="521" y="511">APARTMENTS</text>

    <!-- Address plaque -->
    <g class="panel">
      <rect class="address-plaque" x="84" y="657" width="1032" height="122" fill="url(#plaque-tone)"/>
    </g>
    <rect class="frame-line" x="116" y="678" width="968" height="80"/>
    <text class="address-number" x="611" y="739" text-anchor="middle">28351</text>
  </svg>
  <p class="caption">Design Concept 3</p>
</div>
</body>
</html>
```